I need a new business card designed, we recently rebranded and I need to get a fresh design to match our new logo, colours and branding.

Details:

Derek Havill | Founder & CEO
Address: 7 Marlowfern Lane, #09-14 Tavenport Crest, Singapore 318547
Tel: +65 93568214
Web: www.frostkarta.com.sg
hello@frostkarta.com.sg

I've attached my old card as well

Industry/Entity Type

Business

Requirements
Must have
• Front and Back
Interesting use of logo
Correct use of colour scheme

```html
<!DOCTYPE html>
<html lang="en">
<head>
<meta charset="utf-8">
<title>Frostkarta Business Card – Front and Back</title>
<link rel="stylesheet" href="https://fonts.googleapis.com/css2?family=Arimo:wght@400;700&display=swap">
<style>
  :root {
    --stage: #000000;
    --label: #7a7a7a;
    --card-blue: #29abe2;
    --white: #ffffff;
    --title-blue: #a6dcf5;
  }
  * { margin: 0; padding: 0; box-sizing: border-box; }
  html, body {
    width: 1200px; height: 1000px; overflow: hidden;
    background: var(--stage);
    font-family: "Arimo", Arial, sans-serif;
  }
  .canvas { position: relative; width: 1200px; height: 1000px; }

  .side-label {
    position: absolute; left: 180px;
    font-size: 23px; color: var(--label);
  }
  .side-label--front { top: 76px; }
  .side-label--back { top: 560px; }

  .card {
    position: absolute; left: 286px;
    width: 685px; height: 394px;
    background: var(--card-blue);
    overflow: hidden;
  }
  .card--front { top: 79px; }
  .card--back { top: 557px; }

  .brand-tab {
    position: absolute; height: 118px;
    background: var(--white);
    display: flex; align-items: center; gap: 16px;
  }
  .card--front .brand-tab {
    left: 0; top: 132px; width: 328px;
    border-radius: 0 28px 28px 0;
    padding-left: 22px;
  }
  .card--back .brand-tab {
    left: 345px; top: 134px; width: 340px;
    border-radius: 28px 0 0 28px;
    padding-left: 38px;
  }
  .brand-dot {
    width: 80px; height: 80px; border-radius: 50%;
    background: var(--card-blue); flex: none;
  }
  .brand-name {
    font-size: 34px; font-weight: 700; color: var(--card-blue);
    line-height: 1;
  }

  .person { position: absolute; left: 352px; top: 64px; }
  .person-name {
    font-size: 37px; font-weight: 700; color: var(--white); line-height: 1;
  }
  .person-title {
    margin-top: 5px; font-size: 19px; color: var(--title-blue);
  }

  .contact {
    position: absolute; left: 352px; top: 168px;
    font-size: 16px; color: var(--white); line-height: 22px;
    display: grid; grid-template-columns: 80px 18px auto;
  }
  .contact .gap { grid-column: 1 / 4; height: 21px; }
</style>
</head>
<body>
<main class="canvas">
  <p class="side-label side-label--front">Front</p>
  <section class="card card--front" aria-label="Card front">
    <div class="brand-tab">
      <span class="brand-dot"></span>
      <span class="brand-name">frostkarta</span>
    </div>
    <div class="person">
      <h1 class="person-name">Derek Havill</h1>
      <p class="person-title">Founder &amp; CEO</p>
    </div>
    <div class="contact">
      <span>Tel</span><span>:</span><span>+65 93568214</span>
      <span>Web</span><span>:</span><span>www.frostkarta.com.sg</span>
      <span>e-mail</span><span>:</span><span>hello@frostkarta.com.sg</span>
      <span class="gap"></span>
      <span>Address</span><span>:</span><span>7 Marlowfern Lane,</span>
      <span></span><span></span><span>#09-14 Tavenport Crest,</span>
      <span></span><span></span><span>Singapore 318547</span>
    </div>
  </section>

  <p class="side-label side-label--back">Back</p>
  <section class="card card--back" aria-label="Card back">
    <div class="brand-tab">
      <span class="brand-dot"></span>
      <span class="brand-name">frostkarta</span>
    </div>
  </section>
</main>
</body>
</html>
```